KVOR Individual and Corporate Development Business Card Design

KVOR needs a business card design that is aligned with it's values and targetted markets. Coherent Lattice of Adaptive Reasoning Method's self diagnosis model and tools, which can be used for personal improvement and team/business performance enhancement, is based on the learnings of over 20 years of medical practitioning. KVOR supercharges personal effectiveness and awareness to also increase team and business performance.

The targetted markets are high performance individuals and teams who aspire seek to enhance their capabilities and achieve their absolute best potential.

Look and feel for the business card design we are looking for is high technology, premium, fresh, new and medical.

Target Market(s)

Industry/Entity Type

Business Consultant

Contact Information for Business Card

Logo, Full Name, Title, Phone number, Email, company name, Address,

Font styles to use
Sans Serif

Requirements
Must have
• Tag line: Elevating Capability for Driven High Achievers
• Please use same colours as the logo.

```html
<!DOCTYPE html>
<html lang="en">
<head>
<meta charset="utf-8">
<title>KVOR Business Card</title>
<link href="https://fonts.googleapis.com/css2?family=Roboto:ital,wght@0,400;0,500;0,700;1,400&display=swap" rel="stylesheet">
<style>
  :root {
    --backdrop: #2b2b2c;
    --teal: #03a9c0;
    --slate: #5b5e63;
    --stripe: #58595c;
    --paper: #f3f3f3;
    --white: #ffffff;
  }
  * { margin: 0; padding: 0; box-sizing: border-box; }
  html, body { width: 1200px; height: 960px; overflow: hidden; }
  body {
    background: var(--backdrop);
    font-family: "Roboto", Arial, sans-serif;
    position: relative;
  }
  .card {
    position: absolute;
    width: 600px;
    height: 343px;
    overflow: hidden;
  }
  .card-front { left: 314px; top: 113px; background: var(--paper); }
  .card-back { left: 311px; top: 472px; background: var(--slate); }

  .front-panel { position: absolute; inset: 0; }

  .contact {
    position: absolute;
    left: 32px;
    top: 121px;
    color: var(--white);
  }
  .contact-name { font-size: 20px; font-weight: 500; letter-spacing: 0.2px; line-height: 24px; }
  .contact-title { font-size: 15px; line-height: 20px; margin-bottom: 10px; }
  .contact-company { font-size: 14.5px; font-weight: 500; line-height: 19px; }
  .contact-address { font-size: 14.5px; line-height: 19px; margin-top: 3px; margin-bottom: 8px; }
  .contact-line { display: flex; align-items: center; gap: 7px; font-size: 14.5px; line-height: 19.5px; }
  .contact-line svg { width: 14px; height: 14px; flex: none; }

  .brand { position: absolute; text-align: center; font-weight: 700; }
  .brand-front { left: 300px; top: 58px; width: 270px; color: var(--teal); }
  .brand-back { left: 0; top: 132px; width: 600px; color: var(--white); }
  .brand-mark { font-size: 52px; line-height: 56px; letter-spacing: 3px; }
  .brand-back .brand-mark { font-size: 60px; line-height: 66px; }
  .brand-full { font-size: 12.5px; line-height: 15px; text-transform: uppercase; letter-spacing: 0.4px; margin-top: 8px; }
  .brand-back .brand-full { font-size: 15px; line-height: 18px; margin-top: 12px; }

  .tagline {
    position: absolute;
    left: 0; width: 600px; top: 292px;
    text-align: center;
    color: var(--white);
    font-style: italic;
    font-size: 14.5px;
  }
</style>
</head>
<body>
  <section class="card card-front">
    <svg class="front-panel" width="600" height="343" viewBox="0 0 600 343">
      <polygon points="0,0 166,0 366,343 0,343" fill="var(--teal)"/>
      <polygon points="171,0 179,0 378,343 370,343" fill="var(--stripe)"/>
    </svg>

    <div class="contact">
      <div class="contact-name">DANIEL REEVE</div>
      <div class="contact-title">CEO/FOUNDER</div>
      <div class="contact-company">Coherent Lattice of Adaptive<br>Reasoning Method</div>
      <div class="contact-address">4120 Harbor View Road<br>Juneau, Alaska 99801</div>
      <div class="contact-line">
        <svg viewBox="0 0 16 16"><path fill="#fff" d="M3.6 1.5l2.3 2.6-1.3 1.9c.9 2 2.4 3.6 4.4 4.5l1.9-1.3 2.6 2.3-1.2 2.4C7 13.6 2.4 9 1.1 2.7z"/></svg>
        <span>555 214 7730</span>
      </div>
      <div class="contact-line">
        <svg viewBox="0 0 16 16"><rect x="1.5" y="4" width="13" height="9" fill="#fff"/><path d="M1.5 4l6.5 5 6.5-5" fill="none" stroke="var(--teal)" stroke-width="1.3"/></svg>
        <span>hello@kvormethod.com</span>
      </div>
      <div class="contact-line">
        <svg viewBox="0 0 16 16"><circle cx="8" cy="8" r="6.5" fill="#fff"/><path d="M4.5 5.5c1.5 0 2 1 3 1.5s0 2 1 2.5 1 2 0 3M10 3.5c0 1.5 1.5 2 2.5 2" fill="none" stroke="var(--teal)" stroke-width="1.3"/></svg>
        <span>www.kvormethod.com</span>
      </div>
    </div>

    <div class="brand brand-front">
      <div class="brand-mark">KVOR</div>
      <div class="brand-full">Coherent Lattice of<br>Adaptive Reasoning Method</div>
    </div>
  </section>

  <section class="card card-back">
    <div class="brand brand-back">
      <div class="brand-mark">KVOR</div>
      <div class="brand-full">Coherent Lattice of<br>Adaptive Reasoning Method</div>
    </div>
    <p class="tagline">Elevating Capability for Driven High Achievers</p>
  </section>
</body>
</html>
```